Web design for a relaunch of a technology and knowledge transfer company

Design for the relaunch of an existing website The company specializes in technology and knowledge transfer between companies (and universities). The innovation company (company name) combines many years of experience in technology transfer, innovation management, project management and grant applications. Link: http://www.wandelwerkstatt-beratung.example The colors of the logo are not very advantageous and can be adjusted a bit. There are currently no picture worlds, these are to be selected by the designer. Abstract motifs are certainly an advantage here (10 motifs). Animated programming could be done (network etc. http://ubrexa.plonvimo.example/). In this case a suggestion is made, which we convert programming technically. The structure and contents of the existing pages will be adopted and supplemented. The programming will be done with TYPO3 in responsive form (bootstrap). Required are start page, content page and contact page. -------------------------------------------------- ------------------------------ Web design for a relaunch of a company in technology and knowledge transfer Design for the relaunch of an existing website. The company specializes in technology and knowledge transfer between companies (and universities). The innovation company combines many years of experience in the fields of technology transfer, innovation management, project management and grant application. Link: http://www.wandelwerkstatt-beratung.example The color of the logo is not exactly advantageous and can be adjusted. There are currently no image worlds, these are to be selected by the designer. Abstract motifs are certainly an advantage here (10 motifs). It could also be made animated programming (network, etc. http://ubrexa.plonvimo.example/). In this case, a proposal has to be made, which we implement in terms of programming technology. The structure and contents of the existing pages are taken over and supplemented. Programming is done with TYPO3 in responsive form (bootstrap). Required are homepage, content page and contact page.

```html
<!DOCTYPE html>
<html lang="en">
<head>
<meta charset="utf-8">
<title>Wandelwerkstatt – Technology and Knowledge Transfer</title>
<link href="https://fonts.googleapis.com/css2?family=Lato:wght@400;700;900&display=swap" rel="stylesheet">
<style>
:root{
  --red:#d21f3c;
  --navy:#1f1d6e;
  --blue:#1b19a3;
  --ink:#3a3a4a;
  --muted:#6c6c78;
  --grey:#efeff2;
  --white:#ffffff;
}
*{box-sizing:border-box;margin:0;padding:0}
html,body{width:1200px;height:2756px;overflow:hidden}
body{font-family:'Lato',Arial,sans-serif;color:var(--ink);background:var(--white);position:relative}
a{color:inherit;text-decoration:none}

/* header */
.site-header{height:112px;display:flex;align-items:center;justify-content:space-between;padding:0 60px}
.brand{display:flex;align-items:center;gap:10px}
.brand-mark{width:22px;height:22px;border:3px solid var(--blue)}
.brand-name{font-weight:900;font-size:15px;letter-spacing:1px;color:var(--blue);text-transform:uppercase}
.main-nav{display:flex;gap:34px;font-size:13px;font-weight:700;letter-spacing:.6px;color:var(--navy)}
.main-nav .active{color:var(--red)}

/* hero */
.hero{position:absolute;top:112px;left:0;width:1200px;height:628px;
  background:linear-gradient(160deg,#c9cdd6 0%,#8f939c 35%,#4a4d55 70%,#2b2d33 100%)}
.hero-copy{position:absolute;top:250px;left:0;width:100%;text-align:center;color:var(--white)}
.hero-title{font-size:46px;font-weight:900;letter-spacing:1px}
.hero-lead{margin:16px auto 0;width:720px;font-size:22px;font-weight:700;line-height:1.3}
.hero-dots{position:absolute;bottom:36px;left:0;width:100%;display:flex;justify-content:center;gap:10px}
.hero-dots span{width:10px;height:10px;border-radius:50%;background:rgba(255,255,255,.6)}
.hero-dots span:first-child{background:var(--white)}

/* welcome */
.welcome{position:absolute;top:800px;left:72px;width:1056px;height:500px}
.section-title{font-size:30px;font-weight:900;color:var(--navy);letter-spacing:.5px}
.welcome .section-title::after{content:"";display:block;width:60px;height:3px;background:var(--red);margin-top:8px}
.welcome-text{width:600px;margin-top:16px;font-size:14px;line-height:1.55;color:var(--muted)}
.welcome-question{margin-top:16px;font-size:19px;font-weight:700;color:var(--red)}
.question-list{list-style:none;margin-top:12px;width:610px}
.question-list li{display:flex;gap:10px;font-size:14px;color:var(--ink);line-height:1.4;margin-bottom:8px}
.question-list svg{flex:none;margin-top:2px}
.btn-outline{display:inline-block;border:2px solid var(--red);color:var(--red);font-weight:700;font-size:13px;letter-spacing:1px;padding:12px 36px}
.welcome .btn-outline{margin-top:20px}
.welcome-image{position:absolute;top:20px;right:0;width:400px;height:450px;
  background:linear-gradient(135deg,#d9d9dc,#9c9ea4 60%,#6f7177)}

/* services */
.services{position:absolute;top:1380px;left:0;width:1200px;height:460px;background:var(--grey)}
.title-lined{display:flex;align-items:center;justify-content:center;gap:24px}
.title-lined::before,.title-lined::after{content:"";width:170px;height:1px;background:#b9b9c4}
.services .title-lined{margin-top:28px}
.services-map{position:absolute;top:0;left:0}
.service{position:absolute;display:flex;align-items:center;gap:18px;font-size:15px;font-weight:700;color:var(--navy);text-transform:uppercase;line-height:1.3}
.service.left{flex-direction:row-reverse;text-align:right}
.service.highlight{color:var(--red)}
.service-icon{width:48px;height:48px;border-radius:50%;background:var(--navy);display:flex;align-items:center;justify-content:center;flex:none}
.service.highlight .service-icon{background:var(--red)}
.service-hub{position:absolute;left:480px;top:120px;width:240px;height:240px;border-radius:50%;
  border:6px solid var(--white);background:radial-gradient(circle,#ffffff 30%,#d6d9e6 100%);box-shadow:0 0 0 2px #c7c7d6}

/* reports */
.reports{position:absolute;top:1880px;left:0;width:1200px;height:520px}
.reports .title-lined::before,.reports .title-lined::after{width:150px}
.report-grid{display:flex;gap:40px;padding:0 88px;margin-top:32px}
.report-card{width:320px;position:relative}
.report-image{height:220px;background:linear-gradient(150deg,#8a8d96,#4c4f58 55%,#2a2c33)}
.report-date{position:absolute;left:14px;top:170px;width:64px;text-align:center;font-weight:900}
.report-date .month{display:block;background:var(--navy);color:var(--white);font-size:14px;padding:6px 0}
.report-date .day{display:block;background:var(--red);color:var(--white);font-size:24px;padding:2px 0}
.report-title{margin-top:40px;font-size:18px;font-weight:900;color:var(--navy);line-height:1.3}
.report-more{display:block;margin-top:14px;font-size:12px;font-weight:900;color:var(--navy);letter-spacing:.6px}
.reports-all{text-align:center;margin-top:36px}
.reports-all .btn-outline{padding:10px 32px}

/* footer */
.site-footer{position:absolute;top:2432px;left:0;width:1200px;height:324px;background:var(--blue);color:var(--white);padding:52px 72px 0;display:flex}
.footer-brand{width:260px}
.footer-brand .brand-mark{border-color:var(--white);width:18px;height:18px}
.footer-brand .brand-name{color:var(--white);font-size:12px}
.footer-copy{margin-top:14px;font-size:12px;line-height:1.5;opacity:.85}
.social{display:flex;gap:14px;margin-top:22px}
.social span{width:22px;height:22px;border-radius:50%;background:var(--white);opacity:.9}
.footer-col{width:200px}
.footer-col h3{font-size:18px;font-weight:900;letter-spacing:.5px;margin-bottom:12px}
.footer-col li{list-style:none;font-size:13px;line-height:1.65;opacity:.9}
.footer-col.services-list{width:300px}
.newsletter{width:280px}
.newsletter h3{font-size:22px;font-weight:900;letter-spacing:.5px}
.newsletter p{font-size:13px;line-height:1.45;margin-top:8px;opacity:.9}
.subscribe{display:flex;margin-top:18px}
.subscribe span{width:200px;height:38px;background:var(--white);color:#888;font-size:12px;padding:12px 10px}
.subscribe b{width:56px;height:38px;background:var(--red);font-size:12px;text-align:center;padding-top:12px}
</style>
</head>
<body>

<header class="site-header">
  <div class="brand"><span class="brand-mark"></span><span class="brand-name">Wandelwerkstatt</span></div>
  <nav class="main-nav">
    <a class="active" href="#">HOME</a><a href="#">SERVICES</a><a href="#">REFERENCES</a><a href="#">EVENTS &amp; WORKSHOPS</a><a href="#">REPORTS</a><a href="#">CONTACT</a>
  </nav>
</header>

<section class="hero" role="img" aria-label="Photo of a speaker presenting at a workshop in a lecture room">
  <div class="hero-copy">
    <h1 class="hero-title">THE WANDELWERKSTATT</h1>
    <p class="hero-lead">Is a technology and knowledge transfer company that supports companies in implementing their innovative ideas. We use our large network of scientific institutions.</p>
  </div>
  <div class="hero-dots"><span></span><span></span><span></span></div>
</section>

<section class="welcome">
  <h2 class="section-title">WELCOME !</h2>
  <p class="welcome-text">The Wandelwerkstatt is a technology and knowledge transfer company that supports companies in implementing their innovative ideas. We use our large network of scientific institutions.</p>
  <p class="welcome-question">Maybe you've already wondered in some moments:</p>
  <ul class="question-list">
    <li><svg width="14" height="14" viewBox="0 0 14 14"><path d="M2 7l3 3 7-7" fill="none" stroke="#d21f3c" stroke-width="2.4"/></svg>With whom can I implement my innovative idea?</li>
    <li><svg width="14" height="14" viewBox="0 0 14 14"><path d="M2 7l3 3 7-7" fill="none" stroke="#d21f3c" stroke-width="2.4"/></svg>Who helps me develop new products, services or business models based on my abilities?</li>
    <li><svg width="14" height="14" viewBox="0 0 14 14"><path d="M2 7l3 3 7-7" fill="none" stroke="#d21f3c" stroke-width="2.4"/></svg>How do I become more independent of my existing customers with my own products?</li>
    <li><svg width="14" height="14" viewBox="0 0 14 14"><path d="M2 7l3 3 7-7" fill="none" stroke="#d21f3c" stroke-width="2.4"/></svg>Who protects my ideas?</li>
    <li><svg width="14" height="14" viewBox="0 0 14 14"><path d="M2 7l3 3 7-7" fill="none" stroke="#d21f3c" stroke-width="2.4"/></svg>Who opens the doors to science for me if I do not know who the right people are?</li>
  </ul>
  <a class="btn-outline" href="#">READ MORE</a>
  <div class="welcome-image" role="img" aria-label="Top view of people around a table with a drawn light bulb in the centre"></div>
</section>

<section class="services">
  <h2 class="section-title title-lined">SERVICES</h2>
  <svg class="services-map" width="1200" height="460" viewBox="0 0 1200 460" aria-hidden="true">
    <g fill="none" stroke="#b3b3c6" stroke-width="2">
      <path d="M440 120 Q480 150 505 170"/>
      <path d="M420 240 L478 240"/>
      <path d="M440 360 Q480 330 505 310"/>
      <path d="M760 120 Q720 150 695 170"/>
      <path d="M780 240 L722 240"/>
      <path d="M760 360 Q720 330 695 310"/>
    </g>
  </svg>
  <div class="service-hub" role="img" aria-label="Illustration of a light bulb"></div>

  <div class="service left highlight" style="right:736px;top:96px">
    <span class="service-icon"><svg width="24" height="24" viewBox="0 0 24 24" fill="none" stroke="#fff" stroke-width="2.2"><path d="M19 9a7 7 0 0 0-13-2M5 15a7 7 0 0 0 13 2"/><path d="M6 3v4h4M18 21v-4h-4"/></svg></span>
    <span>Technology &amp;<br>knowledge transfer</span>
  </div>
  <div class="service left" style="right:756px;top:216px">
    <span class="service-icon"><svg width="24" height="24" viewBox="0 0 24 24" fill="none" stroke="#fff" stroke-width="2.2"><rect x="4" y="4" width="16" height="16"/><path d="M8 9h8M8 13h8M8 17h5"/></svg></span>
    <span>Innovation and project<br>management</span>
  </div>
  <div class="service left" style="right:736px;top:336px">
    <span class="service-icon"><svg width="24" height="24" viewBox="0 0 24 24" fill="#fff"><circle cx="8" cy="8" r="3.5"/><circle cx="16" cy="8" r="3.5"/><path d="M2 20c0-4 3-6 6-6s6 2 6 6zM10 20c0-4 3-6 6-6s6 2 6 6z"/></svg></span>
    <span>Cooperation and<br>network management</span>
  </div>

  <div class="service" style="left:736px;top:96px">
    <span class="service-icon"><svg width="24" height="24" viewBox="0 0 24 24" fill="none" stroke="#fff" stroke-width="2.2"><rect x="5" y="10" width="14" height="10"/><path d="M8 10V7a4 4 0 0 1 8 0v3"/></svg></span>
    <span>Property rights<br>and Co.</span>
  </div>
  <div class="service" style="left:756px;top:216px">
    <span class="service-icon"><svg width="24" height="24" viewBox="0 0 24 24" fill="none" stroke="#fff" stroke-width="2.2"><path d="M9 18h6M10 21h4M12 3a6 6 0 0 0-4 10.5V16h8v-2.5A6 6 0 0 0 12 3z"/></svg></span>
    <span>From ideas<br>to innovations</span>
  </div>
  <div class="service" style="left:736px;top:336px">
    <span class="service-icon"><svg width="24" height="24" viewBox="0 0 24 24" fill="none" stroke="#fff" stroke-width="2.4"><path d="M12 3v18M16 7c-1-1.5-7-2-7 1.5S16 11 16 15s-6 3-8 1"/></svg></span>
    <span>All about money<br>promotion</span>
  </div>
</section>

<section class="reports">
  <h2 class="section-title title-lined">REPORTS ON CURRENT TOPICS AND EVENTS</h2>
  <div class="report-grid">
    <article class="report-card">
      <div class="report-image" role="img" aria-label="Photo of a speaker giving a talk"></div>
      <div class="report-date"><span class="month">APR</span><span class="day">04</span></div>
      <h3 class="report-title">Sed pellentesque purus eu nisi porta gravida eget ac leo.</h3>
      <a class="report-more" href="#">READ MORE</a>
    </article>
    <article class="report-card">
      <div class="report-image" role="img" aria-label="Photo of workshop participants talking in a group"></div>
      <div class="report-date"><span class="month">APR</span><span class="day">04</span></div>
      <h3 class="report-title">Sed pellentesque purus eu nisi porta gravida eget ac leo.</h3>
      <a class="report-more" href="#">READ MORE</a>
    </article>
    <article class="report-card">
      <div class="report-image" role="img" aria-label="Photo of event guests standing together"></div>
      <div class="report-date"><span class="month">APR</span><span class="day">04</span></div>
      <h3 class="report-title">Sed pellentesque purus eu nisi porta gravida eget ac leo.</h3>
      <a class="report-more" href="#">READ MORE</a>
    </article>
  </div>
  <div class="reports-all"><a class="btn-outline" href="#">VIEW ALL EVENTS</a></div>
</section>

<footer class="site-footer">
  <div class="footer-brand">
    <div class="brand"><span class="brand-mark"></span><span class="brand-name">Wandelwerkstatt</span></div>
    <p class="footer-copy">Copyright © 2019 Company Name.<br>All rights reserved.</p>
    <div class="social"><span></span><span></span><span></span><span></span><span></span></div>
  </div>
  <div class="footer-col">
    <h3>SITE MAP</h3>
    <ul><li>Home</li><li>Services</li><li>References</li><li>Events &amp; Workshops</li><li>Reports</li><li>Contact</li></ul>
  </div>
  <div class="footer-col services-list">
    <h3>SERVICES</h3>
    <ul><li>Technology and knowledge transfer</li><li>Innovation and project management</li><li>Cooperation and network management</li><li>Property Rights and Co.</li><li>From ideas to innovations</li><li>All about money promotion</li></ul>
  </div>
  <div class="newsletter">
    <h3>NEWSLETTER</h3>
    <p>Stay informed about our latest events, reports and workshop dates.</p>
    <div class="subscribe"><span>Enter Email Address</span><b>GO</b></div>
  </div>
</footer>

</body>
</html>
```